Bring me business with this creative business card

Design my new business card. I am looking for something different with an impact. People will take a look at this card & they will 1- see how different & creative I am, 2-understand what I do 3- Call me to meet me!

I make videos with a message, testimonials. I am dynamic, fun, creative & human. My new website is in construction but in the meantime you can check this old one: brightpath.ca & another one Tidebloom.com & tidebloom facebook page.
I make videos. sometimes with a cameraman, sometimes with my phone. As an ex Public Relations agent, the message is the most important thing for me. I want to make my clients shine! When they start with me they often remind me of a lamb, when I finish coaching them they are powerful like LIONS! That's why I need a powerful business card!

Target Market(s)

Entrepreneurs, solo entrepreneurs, small & medium companies & start ups. People i will meet while networking. People that need videos on their website & social Networks to get attention, to be visible. men & women. From 35 to 49 years old.
I am an ex Public relations agent. I used to send clients in traditional medias, now with videos they have more chances to be seen on google the new media. I do videos of the president, his team, his loyal clients saying how great the company is & expert videos like series so people can be seen for example every 1 st of every month with a short 2 minute video. Also with my 20 years in marketing & communications I can coach & give tips to anybody who needs it.
Target: anybody who would like my old website brightpath.ca & I also have another website but it will be off line soon: tidebloom.com could give you ideas.

Industry/Entity Type

Communications

Contact Information for Business Card

I am in Montreal,So the business cards have to be the usual size like we have in Montreal: 9 cm x 5 cm
Details:My text: Mathilde Tessier Communication coach/Chief Lion. "Creating Videos as unique as you" off: 514-555-0147 cell: 514-555-0183. tidebloom.com
mathilde@tidebloom.com logo facebook, youtube, instagram

Colors
f37122

Requirements
Must have
• Dynamic, happy. Orange. Be creative in the look but NOT the shape of the card. Easy to read. Big enough to read.
Should not have
• No funny shapes: no round, no square, just the usual. I love creative but NOT on shape.

```html
<!DOCTYPE html>
<html lang="en">
<head>
<meta charset="utf-8">
<title>Tidebloom business card</title>
<link rel="stylesheet" href="https://fonts.googleapis.com/css2?family=Roboto:wght@400;500&display=swap">
<style>
  :root {
    --page: #e9e6e2;
    --card: #f6f3ef;
    --orange: #f37122;
    --red-orange: #d4502a;
    --ink: #2b2420;
    --muted: #4a4340;
    --art-a: #f6b45a;
    --art-b: #ec7a4a;
    --art-c: #e2565a;
  }
  * { margin: 0; padding: 0; box-sizing: border-box; }
  html, body { width: 1200px; height: 969px; overflow: hidden; }
  body { background: var(--page); position: relative; font-family: "Roboto", Arial, sans-serif; }

  .card {
    position: absolute; left: 100px; top: 206px;
    width: 1000px; height: 556px;
    background: var(--card);
    overflow: hidden;
    box-shadow: 0 6px 24px rgba(0,0,0,.12);
  }

  .feature-art {
    position: absolute; left: 464px; top: 0; width: 536px; height: 556px;
    background: linear-gradient(160deg, var(--art-b) 0%, var(--art-a) 45%, var(--art-c) 100%);
    opacity: .85;
    clip-path: polygon(12% 0, 100% 0, 100% 100%, 14% 100%, 0 60%);
  }

  .brand-dot {
    position: absolute; left: 128px; top: 52px;
    width: 104px; height: 104px; border-radius: 50%;
    background: var(--orange);
  }
  .brand-name {
    position: absolute; left: 55px; top: 190px; width: 250px;
    text-align: center;
    font-size: 38px; font-weight: 500; letter-spacing: 1px;
    line-height: 48px; color: var(--red-orange);
  }

  .person-name {
    position: absolute; left: 55px; top: 284px;
    font-size: 35px; font-weight: 500; line-height: 44px; color: var(--red-orange);
  }
  .person-role {
    position: absolute; left: 55px; top: 336px;
    font-size: 24px; line-height: 31px; color: var(--orange);
    text-transform: uppercase;
  }

  .contact-list {
    position: absolute; left: 55px; top: 405px; list-style: none;
  }
  .contact-list li {
    display: flex; align-items: center; height: 32px;
    font-size: 22px; color: var(--muted);
  }
  .contact-list svg { width: 22px; height: 22px; margin-right: 14px; fill: var(--red-orange); }

  .slogan {
    position: absolute; left: 540px; top: 440px; width: 370px; text-align: center;
    font-size: 20px; font-weight: 500; color: var(--ink);
  }
  .social-links {
    position: absolute; left: 657px; top: 491px;
    display: flex; gap: 8px; list-style: none;
  }
  .social-links li {
    width: 38px; height: 38px; border-radius: 50%;
    background: var(--red-orange);
  }
</style>
</head>
<body>
  <section class="card" aria-label="Tidebloom business card">
    <div class="feature-art" role="img" aria-label="Large faceted orange and pink geometric backdrop"></div>

    <div class="brand-dot" aria-hidden="true"></div>
    <div class="brand-name">TIDEBLOOM</div>

    <h1 class="person-name">MATHILDE T.</h1>
    <p class="person-role">Communication Coach<br>Chief Lion</p>

    <ul class="contact-list">
      <li><svg viewBox="0 0 24 24" aria-hidden="true"><path d="M6.6 10.8a15 15 0 0 0 6.6 6.6l2.2-2.2a1 1 0 0 1 1-.25 11.4 11.4 0 0 0 3.6.57 1 1 0 0 1 1 1V20a1 1 0 0 1-1 1A17 17 0 0 1 3 4a1 1 0 0 1 1-1h3.5a1 1 0 0 1 1 1c0 1.250.2 2.45.57 3.6a1 1 0 0 1-.25 1z"/></svg>514-555-0147</li>
      <li><svg viewBox="0 0 24 24" aria-hidden="true"><path d="M7 2h10a2 2 0 0 1 2 2v16a2 2 0 0 1-2 2H7a2 2 0 0 1-2-2V4a2 2 0 0 1 2-2zm0 3v13h10V5z"/></svg>514-555-0183</li>
      <li><svg viewBox="0 0 24 24" aria-hidden="true"><path d="M3 5h18a1 1 0 0 1 1 1v12a1 1 0 0 1-1 1H3a1 1 0 0 1-1-1V6a1 1 0 0 1 1-1zm1 2.5V17h16V7.5l-8 5z"/><path d="M4 6.5l8 5 8-5z"/></svg>mathilde@tidebloom.com</li>
      <li><svg viewBox="0 0 24 24" aria-hidden="true"><path d="M12 2a10 10 0 1 0 0 20 10 10 0 0 0 0-20zm6.9 9h-3a15 15 0 0 0-1.3-5.6A8 8 0 0 1 18.9 11zM12 4.1c.9 1.3 1.8 3.6 1.9 6.9h-3.8C10.2 7.7 11.1 5.4 12 4.1zM9.4 5.4A15 15 0 0 0 8.1 11h-3a8 8 0 0 1 4.3-5.6zM5.1 13h3a15 15 0 0 0 1.3 5.6A8 8 0 0 1 5.1 13zm6.9 6.9c-.9-1.3-1.8-3.6-1.9-6.9h3.8c-.1 3.3-1 5.6-1.9 6.9zm2.6-1.3a15 15 0 0 0 1.3-5.6h3a8 8 0 0 1-4.3 5.6z"/></svg>www.tidebloom.com</li>
    </ul>

    <p class="slogan">Creating Videos as unique as you</p>
    <ul class="social-links" aria-label="Social channels">
      <li></li><li></li><li></li>
    </ul>
  </section>
</body>
</html>
```